LEARN Business Skills so you can Earn a good living

size of the poster is 8”x 10.75" plus 0.25" bleed.
Please leave 1 inch on the bottoum for footer
I want a design a poster that will attract people's attention.
I appreciate a creative ad however the ad should not take away from being able to clearly read the text.
-I also appreciate a simple creative ad that is not too busy.
-you can use graphics, vectors, or pictures of real people.
-however, if you use real people it should be a white male that is wearing a white shirt and look like a professional person.

Target Market(s)

Potential young business people

Industry/Entity Type

education

Requirements
Must have
• easy to read the text
Nice to have
• I would like a "creative" simple ad that is easy to be read
Should not have
• pictures of women

```html
<!DOCTYPE html>
<html lang="en">
<head>
<meta charset="utf-8">
<title>Business Enrichment Course – Skillrise Academy</title>
<link rel="stylesheet" href="https://fonts.googleapis.com/css2?family=DM+Sans:wght@400;500;700&family=Playfair+Display:wght@900&family=Dancing+Script:wght@600&display=swap">
<style>
  :root {
    --stage: #d9dadc;
    --paper-top: #f1f1f2;
    --paper-bottom: #e7e7e9;
    --royal: #2a4f9e;
    --navy: #283f77;
    --navy-deep: #1f2d55;
    --orange: #e8912e;
    --ink: #1f2a4d;
    --skyline: #dcdde0;
    --white: #ffffff;
  }
  * { box-sizing: border-box; margin: 0; padding: 0; }
  html, body { width: 1200px; height: 1200px; overflow: hidden; }
  body { background: var(--stage); position: relative; font-family: "DM Sans", sans-serif; }

  .poster {
    position: absolute; left: 195px; top: 30px; width: 810px; height: 1140px;
    background: linear-gradient(180deg, var(--paper-top), var(--paper-bottom));
    overflow: hidden;
  }
  .skyline {
    position: absolute; left: 0; top: 230px; width: 810px; height: 560px;
    background: linear-gradient(180deg, rgba(220,221,224,0) 0%, var(--skyline) 45%, rgba(220,221,224,0.2) 100%);
  }
  .brand-block {
    position: absolute; left: 277px; top: 0; width: 255px; height: 228px;
    background: linear-gradient(180deg, var(--royal), var(--navy));
    border-bottom: 15px solid var(--orange);
    display: flex; flex-direction: column; align-items: center; justify-content: center;
  }
  .brand-name {
    color: var(--white); font-weight: 700; font-size: 38px; line-height: 1.1;
    text-align: center; letter-spacing: 1px;
  }
  .headline {
    position: absolute; left: 0; top: 268px; width: 810px; text-align: center;
    font-family: "Playfair Display", serif; font-weight: 900; color: var(--royal);
    font-size: 80px; line-height: 82px; letter-spacing: -1px;
  }
  .tagline {
    position: absolute; left: 0; top: 522px; width: 810px; text-align: center;
    font-family: "Dancing Script", cursive; font-weight: 600; font-size: 44px;
    color: var(--orange);
  }
  .illustration {
    position: absolute; left: 68px; top: 606px; width: 361px; height: 300px;
    background: linear-gradient(135deg, #e3e6ee 0%, #b9c6e4 50%, #2f56a8 100%);
    border-radius: 6px;
  }
  .benefits { position: absolute; left: 495px; top: 619px; list-style: none; }
  .benefit { display: flex; align-items: center; height: 78px; margin-bottom: 26px; }
  .benefit-icon {
    width: 78px; height: 78px; border-radius: 16px;
    background: linear-gradient(135deg, var(--navy), var(--navy-deep));
    display: flex; align-items: center; justify-content: center; flex-shrink: 0;
  }
  .benefit-label {
    margin-left: 22px; font-weight: 500; font-size: 23px; line-height: 26px; color: var(--ink);
  }
  .course-list {
    position: absolute; left: 40px; top: 940px; width: 730px; text-align: center;
    font-size: 14.5px; line-height: 26.5px; color: var(--ink);
  }
  .course-list .sep { color: var(--orange); margin: 0 3px; }
</style>
</head>
<body>
  <main class="poster">
    <div class="skyline" role="img" aria-label="Faint black-and-white city skyline photo behind the headline"></div>

    <header class="brand-block">
      <div class="brand-name">SKILLRISE<br>ACADEMY</div>
    </header>

    <h1 class="headline">BUSINESS<br>ENRICHMENT<br>COURSE</h1>
    <p class="tagline">A proven success of helping people</p>

    <div class="illustration" role="img" aria-label="Illustration of a businessman with a laptop riding a rising blue arrow over bar chart, with a briefcase"></div>

    <ul class="benefits">
      <li class="benefit">
        <span class="benefit-icon">
          <svg width="50" height="50" viewBox="0 0 50 50" fill="none" stroke="#fff" stroke-width="2.5" stroke-linecap="round">
            <circle cx="22" cy="27" r="17"/>
            <circle cx="20" cy="24" r="5"/>
            <path d="M11 38c2-6 6-8 9-8s7 2 9 8"/>
            <path d="M37 6l2.5 5 5.5.8-4 3.9 1 5.5-5-2.6-5 2.6 1-5.5-4-3.9 5.5-.8z" fill="#e8912e" stroke="#e8912e"/>
          </svg>
        </span>
        <span class="benefit-label">Get a<br>Quality Job</span>
      </li>
      <li class="benefit">
        <span class="benefit-icon">
          <svg width="50" height="50" viewBox="0 0 50 50" fill="none" stroke="#fff" stroke-width="2.5" stroke-linecap="round" stroke-linejoin="round">
            <circle cx="13" cy="14" r="7" fill="#e8912e" stroke="#e8912e"/>
            <path d="M9 17l4-4 2 2 3-3" stroke="#fff" stroke-width="2"/>
            <path d="M6 32h38l-3 9H9z"/>
            <path d="M33 32V10M33 20c-6 0-8-4-8-8 5 0 8 3 8 8zM33 16c5 0 8-3 8-8-5 0-8 3-8 8z"/>
            <path d="M20 32c0-4-3-6-7-6 0 4 3 6 7 6z"/>
          </svg>
        </span>
        <span class="benefit-label">Start/Grow<br>Your Business</span>
      </li>
      <li class="benefit">
        <span class="benefit-icon">
          <svg width="50" height="50" viewBox="0 0 50 50" fill="none" stroke="#fff" stroke-width="2.5" stroke-linecap="round" stroke-linejoin="round">
            <path d="M6 44h38V8"/>
            <path d="M8 40l12-12 6 6 16-18"/>
            <path d="M34 14h9v9"/>
            <path d="M12 6v8M8 10h8M20 14v6M17 17h6" stroke="#e8912e"/>
          </svg>
        </span>
        <span class="benefit-label">Increase<br>Your Salary</span>
      </li>
    </ul>

    <p class="course-list">
      Business Administration<span class="sep">|</span>Small Business Management<span class="sep">|</span>Finance<span class="sep">|</span>Investments<span class="sep">|</span>Computers<span class="sep">|</span>Accounting<span class="sep">|</span><br>
      Sales Marketing<span class="sep">|</span>Project Management Interviewing Skills<span class="sep">|</span>Business Law<span class="sep">|</span>Negotiation<span class="sep">|</span>Public Speaking<span class="sep">|</span><br>
      Import/Export<span class="sep">|</span>Information Technology<span class="sep">|</span>Distribution<span class="sep">|</span>Marketing<span class="sep">|</span>Ledgerly<span class="sep">|</span>Real Estate<span class="sep">|</span>Health Care<span class="sep">|</span><br>
      Management<span class="sep">|</span>Nimbra
    </p>
  </main>
</body>
</html>
```